FunBrixo Business Card

We need a business card design for our company. We sell construction-themed amusement rides for kids.

Contact Information for Business Card

Contact info on business card should include:
Carl Dunning
Co-Founder & COO
(833) 571-FUNBRIX
Carl@funbrixo-demo.com
www.funbrixo-demo.com

```html
<!DOCTYPE html>
<html lang="en">
<head>
<meta charset="utf-8">
<title>FunBrixo Business Card</title>
<link rel="stylesheet" href="https://fonts.googleapis.com/css2?family=Arimo:wght@400;700&display=swap">
<style>
  :root {
    --backdrop: #2b2b2c;
    --card: #262426;
    --orange: #f0561f;
    --brand-orange: #f07a24;
    --text-light: #e4e4e4;
    --divider: #4a4749;
  }
  * { margin: 0; padding: 0; box-sizing: border-box; }
  html, body {
    width: 1200px;
    height: 900px;
    overflow: hidden;
    background: var(--backdrop);
    font-family: "Arimo", Arial, sans-serif;
  }
  .stage {
    position: relative;
    width: 1200px;
    height: 900px;
  }
  .card {
    position: absolute;
    width: 540px;
    height: 309px;
    background: var(--card);
    border-bottom: 9px solid var(--orange);
    box-shadow: 0 14px 30px rgba(0, 0, 0, 0.45);
  }
  .card--front { left: 390px; top: 90px; }
  .card--back { left: 200px; top: 470px; }

  .brand {
    display: flex;
    align-items: center;
    gap: 12px;
    color: var(--brand-orange);
    font-weight: 700;
    letter-spacing: 0.5px;
  }
  .brand__dot {
    width: 22px;
    height: 22px;
    border-radius: 50%;
    background: var(--brand-orange);
    flex: none;
  }
  .card--front .brand {
    position: absolute;
    inset: 0;
    justify-content: center;
    font-size: 64px;
  }
  .card--back .brand {
    position: absolute;
    left: 34px;
    top: 124px;
    font-size: 38px;
  }
  .card--back .brand__dot { width: 16px; height: 16px; }

  .divider {
    position: absolute;
    left: 262px;
    top: 80px;
    width: 1px;
    height: 138px;
    background: var(--divider);
  }
  .contact {
    position: absolute;
    left: 285px;
    top: 84px;
    color: var(--text-light);
  }
  .contact__name {
    color: var(--orange);
    font-weight: 700;
    font-size: 19px;
    letter-spacing: 0.6px;
    text-transform: uppercase;
  }
  .contact__title {
    font-size: 16px;
    margin-top: 3px;
    margin-bottom: 12px;
  }
  .contact__list { list-style: none; }
  .contact__item {
    display: flex;
    align-items: center;
    gap: 8px;
    font-size: 15.5px;
    line-height: 24px;
  }
  .contact__icon {
    width: 15px;
    height: 15px;
    flex: none;
  }
</style>
</head>
<body>
<main class="stage">
  <section class="card card--front" aria-label="Card front">
    <div class="brand">
      <span class="brand__dot"></span>
      <span class="brand__name">FunBrixo</span>
    </div>
  </section>

  <section class="card card--back" aria-label="Card back">
    <div class="brand">
      <span class="brand__dot"></span>
      <span class="brand__name">FunBrixo</span>
    </div>
    <div class="divider"></div>
    <div class="contact">
      <p class="contact__name">Carl Dunning</p>
      <p class="contact__title">Co-Founder &amp; COO</p>
      <ul class="contact__list">
        <li class="contact__item">
          <svg class="contact__icon" viewBox="0 0 16 16" aria-hidden="true">
            <rect x="0.75" y="0.75" width="14.5" height="14.5" rx="2" fill="none" stroke="#f0561f" stroke-width="1.5"/>
            <path d="M5 3.5 L6.8 3.5 L7.4 6 L6.2 7 Q7.2 9 9 9.8 L10 8.6 L12.5 9.2 L12.5 11 Q12 12.5 10.5 12.3 Q4.5 11.3 3.7 5 Q3.6 3.7 5 3.5 Z" fill="#f0561f"/>
          </svg>
          <span>(833) 571-FUNBRIX</span>
        </li>
        <li class="contact__item">
          <svg class="contact__icon" viewBox="0 0 16 16" aria-hidden="true">
            <rect x="0.5" y="3" width="15" height="10.5" fill="#f0561f"/>
            <path d="M0.5 3 L8 9 L15.5 3" fill="none" stroke="#262426" stroke-width="1.3"/>
          </svg>
          <span>Carl@funbrixo-demo.com</span>
        </li>
        <li class="contact__item">
          <svg class="contact__icon" viewBox="0 0 16 16" aria-hidden="true">
            <circle cx="8" cy="8" r="7.5" fill="#f0561f"/>
            <g fill="none" stroke="#262426" stroke-width="1">
              <ellipse cx="8" cy="8" rx="3" ry="7"/>
              <line x1="1" y1="8" x2="15" y2="8"/>
              <line x1="8" y1="1" x2="8" y2="15"/>
              <path d="M2.3 4.5 H13.7 M2.3 11.5 H13.7"/>
            </g>
          </svg>
          <span>www.funbrixo-demo.com</span>
        </li>
      </ul>
    </div>
  </section>
</main>
</body>
</html>
```